Creative, fresh business card design for Ripplecraft Facades

We need a fresh, creative business card design for Ripplecraft Facades. We are the manufacturer of Ripplecraft Facades in Australia. Wall panels are 2400 x 1200mm panels made from MDF and feature 3D patterns on the face of the panel. The colours to be used are green, silver/grey and white RGB
Red 187
Green 207
Blue 65.

An idea is to possibly use a watermark of one of our designs as a background (like on the "Grids" design on the left hand side of page 2 of our brochure).

Target Market(s)

Interior designers, architects, builders and home renovators

Industry/Entity Type

Business

Contact Information for Business Card

Details to go on the card are:
Our logo (attached),
Slogan: "Decorative panels for interiors and exteriors",
Contact name,
Position,
Mobile phone number,
Business address,
Business phone,
Business fax,
Website and
Email address.

I have attached a few images of our panels and our brochure for reference.

The colours of the business card should feature our logo colours which are: RGB
Red 187
Green 207
Blue 65

Requirements
Must have
• Very modern fonts and design. Some of the designs shown especially the "Prisms" design which is a popular design.
Nice to have
• Creative but simple design. Very contemporary.
Should not have
• Anything ornate or old fashioned.

```html
<!DOCTYPE html>
<html lang="en">
<head>
<meta charset="utf-8">
<title>Ripplecraft Facades – Business Card</title>
<link rel="stylesheet" href="https://fonts.googleapis.com/css2?family=Play:wght@400;700&display=swap">
<style>
  :root{
    --backdrop:#808080;
    --card:#fbfbfb;
    --ink:#111111;
    --brand-green:#bbcf41;
    --brand-dark:#3d3d3f;
    --slogan:#9a9a9a;
    --slogan-dark:#5e5a5c;
    --photo-a:#f3d6d8;
    --photo-b:#f7e6e3;
    --photo-c:#efe0cf;
  }
  *{margin:0;padding:0;box-sizing:border-box}
  html,body{width:1200px;height:900px;overflow:hidden;background:var(--backdrop);font-family:"Play",sans-serif}
  .canvas{position:relative;width:1200px;height:900px}
  .card{position:absolute;top:271px;width:457px;height:282px;border-radius:14px;overflow:hidden;
    box-shadow:3px 4px 5px rgba(0,0,0,.45);background:var(--card)}
  .card--front{left:137px}
  .card--back{left:626px}

  .person{position:absolute;left:26px;top:26px;color:var(--ink)}
  .person__name{font-size:26px;font-weight:700;line-height:30px}
  .person__role{font-size:15px;font-weight:700;line-height:18px}

  .contacts{position:absolute;right:27px;top:29px;list-style:none;color:var(--ink);font-size:13.5px}
  .contacts li{display:flex;justify-content:flex-end;align-items:center;gap:6px;height:19px}
  .contacts svg{width:10px;height:10px;flex:none}

  .address{position:absolute;right:26px;top:218px;text-align:right;font-size:13.5px;line-height:19px;color:var(--ink)}

  .brand__mark{position:absolute;display:flex;justify-content:center;align-items:center;gap:6px}
  .brand__square{background:var(--brand-green);flex:none}
  .brand__name{font-weight:700;color:var(--brand-green);white-space:nowrap}
  .brand__slogan{position:absolute;text-align:center;white-space:nowrap}

  .card--front .brand__mark{left:27px;top:146px;width:187px}
  .card--front .brand__square{width:18px;height:18px}
  .card--front .brand__name{font-size:17px}
  .card--front .brand__slogan{left:17px;top:220px;width:207px;font-size:12px;letter-spacing:2px;line-height:14px;color:var(--slogan)}

  .card--back .brand__mark{left:0;top:104px;width:457px;gap:8px}
  .card--back .brand__square{width:30px;height:30px;background:var(--brand-dark)}
  .card--back .brand__name{font-size:27px;color:var(--brand-dark)}
  .card--back .brand__slogan{left:0;top:192px;width:457px;font-size:13.5px;letter-spacing:2.4px;line-height:16px;color:var(--slogan-dark)}

  .panel-photo{position:absolute;inset:0;
    background:linear-gradient(100deg,var(--photo-a) 0%,var(--photo-b) 55%,var(--photo-c) 100%)}
</style>
</head>
<body>
<main class="canvas">
  <section class="card card--front" aria-label="Card front">
    <div class="person">
      <h1 class="person__name">Liam Hartley</h1>
      <p class="person__role">Director</p>
    </div>
    <ul class="contacts">
      <li>712-5550-184
        <svg viewBox="0 0 10 10"><rect x="2.5" y=".5" width="5" height="9" rx="1" fill="none" stroke="currentColor"/><rect x="4" y="7.5" width="2" height=".8" fill="currentColor"/></svg></li>
      <li>717-(555)-203
        <svg viewBox="0 0 10 10"><path d="M1 3.5Q5 .5 9 3.5V5H7V4H3V5H1Z" fill="currentColor"/><rect x="2" y="5.5" width="6" height="3.5" rx=".6" fill="currentColor"/></svg></li>
      <li>717-(555)-204
        <svg viewBox="0 0 10 10"><rect x="3" y="1" width="4" height="3" fill="none" stroke="currentColor"/><rect x="1" y="4" width="8" height="5" rx=".8" fill="currentColor"/></svg></li>
      <li>info@ripplecraft.au
        <svg viewBox="0 0 10 10"><rect x=".5" y="2" width="9" height="6.5" fill="currentColor"/><path d="M.8 2.3L5 5.6 9.2 2.3" fill="none" stroke="#fff" stroke-width=".9"/></svg></li>
      <li>www.ripplecraft.au
        <svg viewBox="0 0 10 10"><circle cx="5" cy="5" r="4.5" fill="currentColor"/><path d="M.8 5H9.2M5 .6Q2.5 5 5 9.4M5 .6Q7.5 5 5 9.4" fill="none" stroke="#fff" stroke-width=".6"/></svg></li>
    </ul>
    <div class="brand__mark"><span class="brand__square"></span><span class="brand__name">Ripplecraft Facades</span></div>
    <p class="brand__slogan">sculpted boards for<br>rooms &amp; outdoor living</p>
    <p class="address">18 Harbour Lane,<br>Geelong VIC 3220</p>
  </section>

  <section class="card card--back" aria-label="Card back">
    <div class="panel-photo" role="img" aria-label="Faded photo of an interior with a pyramid-patterned 3D wall panel"></div>
    <div class="brand__mark"><span class="brand__square"></span><span class="brand__name">Ripplecraft Facades</span></div>
    <p class="brand__slogan">sculpted boards for<br>rooms &amp; outdoor living</p>
  </section>
</main>
</body>
</html>
```